Flyer für ambulanten Pflegedienst
Zielgruppe
Ambulanter Pflegedienst, Potentielle Kunden für Grund- und Behandlungspflege, nicht nur Pflegebedürftige, sondern auch Angehörige. Flyer dient zur Auslage, beispielsweise in Wartezimmern von Ärzten.
Aufgabenstellung
Ausführliches Briefing mit Aufbau und Text in der Anlage, ebenso das Bildmaterial, Fonts, Logos. Flyer in A4 Wickelfalz, bitte die Gestaltungsvorlage mit den Maßen des Druckanbieters (ebenfalls anbei) beachten. Vorerst hauptsächlich KI-generierte/Stockfotos vorhanden, Fotoshooting folgt im Juli und Bilder werden dann ggf. nochmal ersetzt um persönliche Ebene zu erzeugen. Der erste Wurf muss aber vorerst so erfolgen. Übergabe der Daten: Druckfähiges PDF, PDF mit Ebenen und AI

```html
<!DOCTYPE html>
<html lang="de">
<head>
<meta charset="utf-8">
<title>Flyer Hauskrankenpflege Hallberg</title>
<link href="https://fonts.googleapis.com/css2?family=Outfit:wght@300;400;500;600&display=swap" rel="stylesheet">
<style>
:root{
  --blue:#123f93;
  --blue-dark:#0e3683;
  --blue-line:#2f66c9;
  --ink:#15409a;
  --grey:#6d6f78;
  --pale:#e9eef7;
  --bg:#d3d3d3;
  --white:#ffffff;
}
*{margin:0;padding:0;box-sizing:border-box}
html,body{width:960px;height:1200px;overflow:hidden;background:var(--bg)}
body{font-family:"Outfit",sans-serif;position:relative}
.sheet{position:absolute;left:120px;width:720px;height:556px;display:flex}
.sheet--outside{top:36px}
.sheet--inside{top:608px}
.panel{position:relative;height:100%;overflow:hidden}
.panel--light{background:linear-gradient(90deg,var(--white) 80%,#f1f1f3);color:var(--ink)}
.panel--blue{background:var(--blue);color:var(--white)}
.abs{position:absolute}
.heading{font-weight:600;font-size:15px;line-height:18.5px}
.body{font-weight:300;font-size:9.6px;line-height:15.5px}
.body--regular{font-weight:400}
.grey{color:var(--grey)}
.rule{position:absolute;height:1px;background:var(--blue-line)}
.rule--grey{background:#a7a9b0}
.swoosh{position:absolute;inset:0;width:100%;height:100%}
.logo{position:absolute;left:0;right:0;text-align:center;color:var(--blue);font-weight:500;font-size:17px;line-height:20px}
.logo__dot{display:inline-block;width:9px;height:9px;border-radius:50%;background:var(--blue);margin-right:6px;vertical-align:1px}
.logo small{display:block;font-size:10px;font-weight:500;letter-spacing:.5px}
.photo{position:absolute}
.checklist{list-style:none}
.check{position:absolute;left:18px;width:202px;padding-left:19px}
.check svg{position:absolute;left:0;top:2px;width:12px;height:12px}
.hero-title{font-weight:600;font-size:25px;line-height:27.5px;color:var(--blue)}
.hero-sub{font-weight:500;font-size:13.5px;line-height:20px;color:var(--blue)}
.bullets{list-style:none;color:var(--grey);font-weight:300;font-size:11px;line-height:17.5px}
.bullets li::before{content:"";display:inline-block;width:5px;height:5px;border-radius:50%;background:var(--blue);margin-right:10px;vertical-align:2px}
.quote-band{position:absolute;left:0;right:0;top:179px;height:64px;background:var(--pale)}
.quote{position:absolute;left:33px;top:17px;width:205px;font-weight:600;font-size:9.8px;line-height:15.5px;color:var(--blue)}
</style>
</head>
<body>

<!-- Outside of the fold -->
<section class="sheet sheet--outside">
  <div class="panel panel--light" style="width:236px">
    <h2 class="heading abs" style="left:33px;top:30px">Pflege braucht Vertrauen.<br>Und Menschen, die da sind.</h2>
    <p class="body body--regular abs" style="left:33px;top:86px;width:200px">Bei der Hauskrankenpflege Hallberg arbeiten über 40 engagierte Mitarbeitende Hand in Hand – mit Herz, Respekt und fachlicher Kompetenz.</p>
    <p class="body body--regular abs" style="left:34px;top:205px;width:195px">Wir sind für Sie da.<br>Sie möchten sich informieren oder ein persönliches Gespräch vereinbaren? Wir beraten Sie gerne – unkompliziert, persönlich und unverbindlich.</p>
    <div class="rule" style="left:34px;top:329px;width:77px"></div>
    <h3 class="heading abs" style="left:34px;top:381px">Kontakt</h3>
    <p class="body body--regular abs" style="left:33px;top:417px;width:200px">Hauskrankenpflege Hallberg<br>Lindenhof 10, 31999 Tannrode<br>Telefon: 0 5999-12 93 0<br>info@hallberg-pflege.de<br>www.hallberg-pflege.de<br>Bürozeiten: Mo., Di., Mi., Fr. 9 bis 12 Uhr und Do. 15 bis 17 Uhr</p>
  </div>

  <div class="panel panel--blue" style="width:238px">
    <svg class="swoosh" viewBox="0 0 238 556" aria-hidden="true">
      <path d="M14 370 C60 300 150 280 238 290 L238 300 C160 292 80 310 14 370Z" fill="#1a4aa3"/>
      <path d="M0 560 C80 520 200 440 238 330 L238 556Z" fill="#1747a0" opacity=".6"/>
    </svg>
    <h2 class="heading abs" style="left:18px;top:30px">Hilfe im Haushalt.<br>Entlastung im Alltag.</h2>
    <p class="body abs" style="left:18px;top:86px;width:210px">Damit Sie sich zuhause weiterhin wohlfühlen können, bieten wir fachgerechte und zuverlässige Unterstützung:</p>
    <ul class="checklist">
      <li class="check body" style="top:158px"><svg viewBox="0 0 12 12"><rect x="1" y="1.5" width="9.5" height="9.5" rx="2.5" fill="none" stroke="#6fa4ff" stroke-width="1"/><path d="M3.5 6l2 2L11 1.5" fill="none" stroke="#6fa4ff" stroke-width="1.2"/></svg>Hilfe im Haushalt: Von der Grundreinigung bis zur Wäschepflege.</li>
      <li class="check body" style="top:205px"><svg viewBox="0 0 12 12"><rect x="1" y="1.5" width="9.5" height="9.5" rx="2.5" fill="none" stroke="#6fa4ff" stroke-width="1"/><path d="M3.5 6l2 2L11 1.5" fill="none" stroke="#6fa4ff" stroke-width="1.2"/></svg>Alltagsbegleitung: Gesellschaft und Unterstützung, wenn gewünscht.</li>
      <li class="check body" style="top:251px"><svg viewBox="0 0 12 12"><rect x="1" y="1.5" width="9.5" height="9.5" rx="2.5" fill="none" stroke="#6fa4ff" stroke-width="1"/><path d="M3.5 6l2 2L11 1.5" fill="none" stroke="#6fa4ff" stroke-width="1.2"/></svg>Betreuung: Strukturierte Hilfe nach individuellem Bedarf.</li>
    </ul>
    <div class="rule" style="left:18px;top:197px;width:202px"></div>
    <div class="rule" style="left:18px;top:243px;width:202px"></div>
    <h3 class="heading abs" style="left:18px;top:404px">Kontakt</h3>
    <p class="body abs" style="left:18px;top:450px;width:215px">So erreichen Sie uns:<br>Telefon: 0 5999-94 96 812<br>info@hallberg-hausdienste.de<br>www.hallberg-hausdienste.de<br>Bürozeiten: Mo., Di., Do., Fr. 8 bis 11 Uhr</p>
  </div>

  <div class="panel" style="width:246px;background:var(--white)">
    <div class="photo" role="img" aria-label="Foto: Pflegekraft im Gespräch mit einer lächelnden älteren Frau im Wohnzimmer, Zimmerpflanzen im Hintergrund" style="left:0;top:0;width:246px;height:400px;background:linear-gradient(180deg,rgba(255,255,255,0) 25%,#fff 92%),linear-gradient(90deg,#dfe3e6 0%,#b9c6cf 30%,#8fb3a8 60%,#e7ece9 100%)"></div>
    <div class="logo" style="top:40px"><span class="logo__dot"></span>Hallberg<small>Hauskrankenpflege</small></div>
    <h1 class="hero-title abs" style="left:14px;top:302px">Weil das<br>eigene Zuhause<br>Lebensqualität ist.</h1>
    <p class="hero-sub abs" style="left:14px;top:407px;width:225px">Ihr ambulanter Pflegedienst für die Region Tannrode und Birkenfeld.</p>
    <ul class="bullets abs" style="left:14px;top:475px">
      <li>24h erreichbar</li>
      <li>Persönliche Beratung</li>
      <li>MD-geprüfte Qualität</li>
    </ul>
  </div>
</section>

<!-- Inside of the fold -->
<section class="sheet sheet--inside">
  <div class="panel panel--light" style="width:244px">
    <h2 class="heading abs" style="left:33px;top:30px">Wer wir sind</h2>
    <p class="body grey abs" style="left:33px;top:65px">Vertrauen beginnt mit Zuhören.</p>
    <p class="body grey abs" style="left:33px;top:98px;width:208px">Pflege bedeutet für uns mehr als Versorgung. Deshalb nehmen wir uns Zeit für persönliche Gespräche und individuelle Lösungen, die zu Ihrem Leben passen.</p>
    <div class="quote-band"><p class="quote">”Unsere Pflege orientiert sich am Befinden der Menschen – nicht am Befund.”</p></div>
    <div class="photo" role="img" aria-label="Foto: Pflegerin in blauer Dienstkleidung im Gespräch mit einer älteren Dame" style="left:0;top:243px;width:244px;height:313px;background:linear-gradient(135deg,#b98a5c 0%,#d9b48c 35%,#2a5fb4 65%,#c9c2b8 100%)"></div>
  </div>

  <div class="panel panel--blue" style="width:240px">
    <svg class="swoosh" viewBox="0 0 240 556" aria-hidden="true">
      <path d="M0 100 C70 40 160 15 240 12 L240 22 C160 28 80 55 0 100Z" fill="#1a4aa3"/>
      <path d="M0 340 C80 300 180 280 240 260 L240 556 L0 556Z" fill="#0f3a8a" opacity=".5"/>
      <path d="M0 170 C60 140 110 130 130 132 C100 135 50 150 0 185Z" fill="#1a4aa3"/>
    </svg>
    <h2 class="heading abs" style="left:14px;top:30px">Unsere Leistungen</h2>
    <p class="body abs" style="left:14px;top:65px">Unterstützung, die den Alltag leichter macht.</p>
    <div class="rule" style="left:14px;top:123px;width:77px"></div>
    <p class="body abs" style="left:14px;top:169px;width:215px">Grundpflege: Unterstützung bei Körperpflege, Mobilität und Ernährung.</p>
    <div class="rule" style="left:14px;top:206px;width:212px"></div>
    <p class="body abs" style="left:14px;top:215px;width:215px">Behandlungspflege: Medizinische Versorgung nach ärztlicher Verordnung (z.B. Wundversorgung, Medikamentengabe).</p>
    <div class="rule" style="left:14px;top:268px;width:212px"></div>
    <p class="body abs" style="left:14px;top:277px;width:215px">Betreuung &amp; Alltagsbegleitung: Stundenweise Betreuung, Unterstützung bei Demenz und Entlastung für Angehörige.</p>
    <div class="photo" role="img" aria-label="Foto: lächelnde Haushaltshilfe mit Putzeimer und Reinigungsmitteln" style="left:14px;top:390px;width:211px;height:127px;background:linear-gradient(90deg,#dfe6ea 0%,#a9c1c5 40%,#2f6b4f 70%,#cfd9dc 100%)"></div>
  </div>

  <div class="panel" style="width:236px;background:linear-gradient(90deg,#fff 85%,#f2f2f4)">
    <div class="logo" style="top:42px"><span class="logo__dot"></span>Hallberg<small>Hauskrankenpflege</small></div>
    <div class="photo" role="img" aria-label="Foto: Pflegerin in grünem Shirt mit älterer Dame auf einer Gartenbank" style="left:11px;top:176px;width:211px;height:126px;background:linear-gradient(160deg,#4d6b35 0%,#7da14a 45%,#6f9b3e 70%,#c9b7c0 100%)"></div>
    <p class="body grey abs" style="left:11px;top:342px;width:215px">Verhinderungspflege: Auszeiten für pflegende Angehörige, um mal durchzuatmen.</p>
    <div class="rule rule--grey" style="left:11px;top:379px;width:211px"></div>
    <p class="body grey abs" style="left:11px;top:388px;width:215px">Beratung: Pflegeberatung nach § 37.3 SGB XI, Hilfe bei Anträgen und Fragen.</p>
    <div class="rule rule--grey" style="left:11px;top:428px;width:211px"></div>
    <p class="body grey abs" style="left:11px;top:434px;width:215px">Hausnotruf &amp; Palliative Versorgung: Sicherheit rund um die Uhr und spezialisierte Begleitung zum Ende des Lebens.</p>
  </div>
</section>

</body>
</html>
```